AUTOMOTIVE/ CAR REPAIRS / CRASH REPAIRS / PAINT SPRAYING AND PANEL BEATING

AUTOMOTIVE REPAIR. CAR / MOTORCYCLES GOT LOGO DESIGN / DID THINK ABOUT FACEBOOK DONT NOALREADY HAVE WEB ADRESS www.brenvashine.co.uk and mail sales@brenvashine,co.uk NEED SOMETHINK I CAN MANAGE TO UPLOAD PICTURES IN TO A GALLERY OR SOMETHINGLIKE THAT I ALSO SELL CAR AND MOTORCYCLES MAYBE A SELLS PAGE WITH A TILLWAVE LINK

Target Market(s)

TRADE / GENERAL PUBLIC

Industry/Entity Type

Automotive

Coding

Coded - Design and coding required

Number of Pages Required

4 page

Font styles to use
Serif
Sans Serif

Colors

Designer to choose colors to be used in the design.

Requirements
Must have
• GALLERY/ SHOP TO SALE CARS AND MOTORCYCLE / LOGOS OF MATERIALS I USE DORFLINT / KEBO / VASTINCO / Q WRAP / GLENBRUSH
• CONTACT US
Nice to have
• TILLWAVE / EASY TO MANAGE / VIDEO CLIP OF DORFLINT HUE PLANNER Z7
• SWIFT BLEND PAINT TONVIEW WETLINE AND TULVOKE

```html
<!DOCTYPE html>
<html lang="en">
<head>
<meta charset="utf-8">
<title>Brenvashine Body Shop</title>
<link href="https://fonts.googleapis.com/css2?family=Josefin+Sans:wght@400;600;700&display=swap" rel="stylesheet">
<style>
:root{
  --navy:#1e2433;
  --navy-deep:#171c28;
  --red:#e8342f;
  --white:#ffffff;
  --muted:#c9ccd3;
  --black:#101216;
}
*{box-sizing:border-box;margin:0;padding:0}
html,body{width:1200px;height:4317px;overflow:hidden}
body{position:relative;background:var(--navy);color:var(--white);font-family:"Josefin Sans",Arial,sans-serif}
h2,h3,h4{font-weight:400}
.abs{position:absolute}
.pill{position:absolute;border-radius:28px;display:flex;align-items:center;justify-content:center;gap:10px;font-weight:600;color:var(--white)}
.pill svg{width:18px;height:18px}
.center{text-align:center;left:0;width:1200px}

/* header */
.topbar{left:0;top:0;width:1200px;height:38px;background:var(--navy-deep)}
.social{top:8px;display:flex;gap:12px;left:984px}
.social span{width:22px;height:22px;background:#2b3140;border-radius:2px}
.header-left{left:0;top:38px;width:330px;height:81px;background:var(--navy-deep)}
.brand{left:97px;top:66px;font-size:24px;font-weight:600;letter-spacing:2px;color:var(--white)}
.navband{left:0;top:38px;width:1200px;height:81px;background:var(--red);clip-path:polygon(370px 0,1200px 0,1200px 81px,410px 81px)}
.stripes{left:300px;top:38px}
.nav{top:68px;left:413px;display:flex;gap:36px;font-size:18px}
.nav a{color:var(--white);text-decoration:none}

/* hero */
.hero-photo{left:0;top:119px;width:1200px;height:581px;
  background:
    radial-gradient(ellipse 260px 330px at 930px 330px,#24314d 0%,#22304a 55%,transparent 75%),
    radial-gradient(ellipse 120px 150px at 790px 530px,#d9c24a 0%,#b9a23a 50%,transparent 80%),
    radial-gradient(ellipse 420px 200px at 330px 120px,#5e6572 0%,transparent 80%),
    radial-gradient(ellipse 300px 300px at 1130px 250px,#8a9aae 0%,transparent 80%),
    linear-gradient(100deg,#2b3140 0%,#454d5c 40%,#6d7686 68%,#3a4455 100%)}
.hero-title{left:110px;top:310px}
.hero-title .welcome{font-size:36px;font-weight:600;display:block}
.hero-title .name{font-size:54px;font-weight:600;display:block;margin-top:2px}
.hero-title .line{font-size:26px;font-weight:600;display:block;margin-top:10px}
.store-band{left:0;top:637px;width:856px;height:129px;background:var(--red);clip-path:polygon(0 0,788px 0,856px 129px,0 129px)}
.store-icon{left:87px;top:660px}
.store-title{left:198px;top:656px;font-size:28px;font-weight:600}
.store-text{left:198px;top:692px;font-size:15px;line-height:28px;width:330px}
.btn-dark{background:var(--black)}

/* about */
.emblem{left:98px;top:860px;width:370px;height:370px;border-radius:50%;border:14px solid var(--red);display:flex;align-items:center;justify-content:center;font-size:30px;font-weight:600;letter-spacing:2px;color:var(--white)}
.about-title{left:538px;top:900px;font-size:38px}
.about-title b{font-weight:600}
.about-text{left:538px;top:958px;width:572px;font-size:16px;line-height:34px;text-align:justify}
.btn-red{background:var(--red)}
.divider{left:89px;width:1021px;height:1px;background:#3c4356}

/* section heads */
.sec-title{font-size:40px}
.sec-title b{font-weight:600}
.sec-desc{font-size:16px;line-height:31px;left:130px;width:940px;text-align:center}

/* services */
.service{width:318px;text-align:center}
.service .icon{width:72px;height:72px;background:var(--red);margin:0 auto;display:flex;align-items:center;justify-content:center}
.service h3{font-size:16px;font-weight:600;margin-top:26px;text-transform:uppercase}
.service p{font-size:13px;line-height:25px;margin-top:6px;color:var(--muted)}

/* gallery */
.ticks{left:0;width:1200px;height:33px;border-top:1px solid #8a909c;border-bottom:1px solid #8a909c;opacity:.6}
.gallery-bg{left:0;top:2011px;width:1200px;height:805px;
  background:radial-gradient(ellipse 500px 300px at 200px 100px,#4a505d 0%,transparent 80%),
  radial-gradient(ellipse 400px 300px at 1000px 150px,#454b58 0%,transparent 80%),
  linear-gradient(180deg,#373d4b 0%,#2a3040 50%,#20263a 100%)}
.tabs{top:2241px;left:305px;display:flex;gap:10px}
.tab{height:35px;padding:0 18px;background:#242a37;font-size:17px;display:flex;align-items:center;font-weight:600}
.tab.active{background:var(--red)}
.shot{position:absolute}

/* partners */
.partner{position:absolute;top:3037px;width:191px;height:84px;background:var(--white);color:var(--navy);font-weight:700;font-size:22px;display:flex;align-items:center;justify-content:center;letter-spacing:1px}
.pager{left:552px;top:3146px;display:flex;gap:10px;align-items:center}
.pager .dot{width:12px;height:12px;border-radius:50%;border:2px solid var(--white)}
.pager .dot.on{background:var(--red);border-color:var(--red)}

/* blog */
.post{position:absolute;top:3394px;width:328px}
.post .img{height:193px}
.post .date{position:absolute;left:16px;top:178px;background:var(--red);font-size:14px;padding:6px 10px}
.post h3{font-size:17px;font-weight:600;margin:46px 16px 0;white-space:nowrap}
.post p{font-size:12.5px;line-height:25px;margin:8px 16px 0;color:var(--muted);text-align:justify}
.post .more{display:block;font-size:13px;font-weight:700;margin:10px 16px 0}

/* appointment */
.appt-photo{left:0;top:3831px;width:520px;height:129px;
  background:radial-gradient(circle 45px at 70px 70px,#3a3e46 0%,#3a3e46 60%,transparent 62%),
  radial-gradient(circle 45px at 400px 60px,#3a3e46 0%,#3a3e46 60%,transparent 62%),
  linear-gradient(90deg,#b8bdc4,#8b9099 50%,#c2c6cc)}
.appt-band{left:444px;top:3831px;width:756px;height:129px;background:var(--red);clip-path:polygon(0 0,756px 0,756px 129px,76px 129px)}
.appt-title{left:558px;top:3850px;font-size:28px;font-weight:600}
.appt-text{left:558px;top:3890px;font-size:15px;line-height:28px;width:330px}

/* footer */
.footer{left:0;top:3960px;width:1200px;height:290px;background:var(--navy-deep)}
.fcol{top:4004px}
.fcol h4{font-size:15px;font-weight:700;margin-bottom:16px}
.fcol li{list-style:none;font-size:15px;line-height:31px}
.fcol li::before{content:"";display:inline-block;border-left:5px solid var(--white);border-top:4px solid transparent;border-bottom:4px solid transparent;margin-right:8px}
.contact-row{position:absolute;left:865px;display:flex;gap:15px;align-items:center;font-size:13px;line-height:20px;width:250px}
.contact-row .ico{flex:none;width:30px;height:30px;background:var(--red);display:flex;align-items:center;justify-content:center}
.bottombar{left:0;top:4250px;width:1200px;height:67px;background:#12161f}
.legal{left:91px;top:4262px;font-size:13px;line-height:26px}
.pay{left:1060px;top:4274px;width:56px;height:30px;background:var(--white);color:var(--navy);font-size:9px;font-weight:700;display:flex;align-items:center;justify-content:center}
</style>
</head>
<body>

<header>
  <div class="abs topbar"></div>
  <div class="abs social" aria-label="Social links"><span></span><span></span><span></span><span></span></div>
  <div class="abs navband"></div>
  <div class="abs header-left"></div>
  <svg class="abs stripes" width="110" height="81" viewBox="0 0 110 81" aria-hidden="true">
    <polygon points="10,0 22,0 72,81 60,81" fill="#e8342f"/>
    <polygon points="30,0 42,0 92,81 80,81" fill="#e8342f"/>
    <polygon points="50,0 62,0 112,81 100,81" fill="#e8342f"/>
  </svg>
  <div class="abs brand">BRENVASHINE</div>
  <nav class="abs nav">
    <a>Home</a><a>About Us</a><a>Service</a><a>Custom</a><a>Gallery</a><a>Our Store</a><a>Contact</a>
  </nav>
</header>

<section class="hero">
  <div class="abs hero-photo" role="img" aria-label="Mechanic inspecting the underside of a car on a lift"></div>
  <div class="abs hero-title">
    <span class="welcome">Welcome to</span>
    <span class="name">Brenvashine Body Shop</span>
    <span class="line">Your one stop body shop</span>
    <span class="line">The home of paint perfection</span>
  </div>
  <div class="abs store-band"></div>
  <svg class="abs store-icon" width="93" height="78" viewBox="0 0 93 78" fill="none" stroke="#fff" stroke-width="3" aria-hidden="true">
    <path d="M6 4h81l4 18H2z"/><path d="M8 22v52h77V22"/><rect x="16" y="36" width="22" height="38"/><rect x="48" y="36" width="28" height="20"/>
  </svg>
  <div class="abs store-title">Our Store</div>
  <div class="abs store-text">Sed ut perspiciatis unde omnis iste natus sit voluptatem accusantium dolorem.</div>
  <div class="pill btn-dark" style="left:543px;top:674px;width:205px;height:53px;font-size:19px">Our Products
    <svg viewBox="0 0 20 20"><circle cx="10" cy="10" r="10" fill="#fff"/><path d="M8 5l5 5-5 5" stroke="#101216" stroke-width="2.5" fill="none"/></svg></div>
</section>

<section class="about">
  <div class="abs emblem">BRENVASHINE</div>
  <h2 class="abs about-title">About <b>BRENVASHINE</b></h2>
  <p class="abs about-text">Equipped with the latest technology and factory trained technicians, we process accident repairs for all leading insurance and vehicle management companies, specialising in accident repairs for most prestige vehicles manufacturers. We are proud to maintain a close working partnership with several local dealership networks.</p>
  <div class="pill btn-red" style="left:538px;top:1145px;width:206px;height:53px;font-size:19px">Read More
    <svg viewBox="0 0 20 20"><circle cx="10" cy="10" r="10" fill="#fff"/><path d="M8 5l5 5-5 5" stroke="#e8342f" stroke-width="2.5" fill="none"/></svg></div>
  <div class="abs divider" style="top:1339px"></div>
</section>

<section class="services">
  <h2 class="abs center sec-title" style="top:1415px">Our <b>Services</b></h2>
  <p class="abs sec-desc" style="top:1475px">Sed ut perspiciatis unde omnis iste natus error sit voluptatem accusantium doloremque laudantium, totam rem aperiam, eaque ipsa quae ab illo inventore veritatis et quasi architecto beatae vitae dicta sunt explicabo.</p>

  <div class="abs service" style="left:82px;top:1580px"><div class="icon" role="img" aria-label="Air conditioning icon">
    <svg width="50" height="50" viewBox="0 0 50 50" fill="none" stroke="#fff" stroke-width="2.2"><circle cx="25" cy="25" r="21"/><circle cx="25" cy="25" r="14"/><path d="M25 15v20M16 20l18 10M16 30l18-10"/></svg></div>
    <h3>Air Conditioning</h3><p>Lorem ipsum dolor sit amet, consectetur adipiscing elit, sed do eiusmod dolore magna aliqua.</p></div>
  <div class="abs service" style="left:436px;top:1580px"><div class="icon" role="img" aria-label="Brake disc icon">
    <svg width="50" height="50" viewBox="0 0 50 50" fill="none" stroke="#fff" stroke-width="2.2"><circle cx="25" cy="25" r="21"/><circle cx="25" cy="25" r="6"/><circle cx="25" cy="13" r="2.5"/><circle cx="36" cy="25" r="2.5"/><circle cx="25" cy="37" r="2.5"/><circle cx="14" cy="25" r="2.5"/><path d="M40 10a20 20 0 0 1 6 12"/></svg></div>
    <h3>Brake Repair</h3><p>Lorem ipsum dolor sit amet, consectetur adipiscing elit, sed do eiusmod dolore magna aliqua.</p></div>
  <div class="abs service" style="left:791px;top:1580px"><div class="icon" role="img" aria-label="Oil filter icon">
    <svg width="50" height="50" viewBox="0 0 50 50" fill="none" stroke="#fff" stroke-width="2.2"><rect x="14" y="6" width="22" height="8" rx="2"/><rect x="12" y="14" width="26" height="30" rx="3"/><path d="M18 20h14M18 26h14M18 32h14M18 38h14"/></svg></div>
    <h3>Lube, Oil and Filters</h3><p>Lorem ipsum dolor sit amet, consectetur adipiscing elit, sed do eiusmod dolore magna aliqua.</p></div>
  <div class="abs service" style="left:82px;top:1770px"><div class="icon" role="img" aria-label="Belts and hoses icon">
    <svg width="50" height="50" viewBox="0 0 50 50" fill="none" stroke="#fff" stroke-width="2.2"><circle cx="16" cy="34" r="8"/><circle cx="34" cy="14" r="6"/><path d="M10 28L29 9M22 40L40 19"/><rect x="8" y="44" width="34" height="3"/></svg></div>
    <h3>Belts and Hoses</h3><p>Lorem ipsum dolor sit amet, consectetur adipiscing elit, sed do eiusmod dolore magna aliqua.</p></div>
  <div class="abs service" style="left:436px;top:1770px"><div class="icon" role="img" aria-label="Engine diagnostics icon">
    <svg width="50" height="50" viewBox="0 0 50 50" fill="none" stroke="#fff" stroke-width="2.2"><path d="M8 18h8l4-5h12l4 5h6v16h-6l-4 5H20l-4-5H8z"/><circle cx="25" cy="26" r="6"/><path d="M4 22v8M46 22v8"/></svg></div>
    <h3>Engine Diagnostics</h3><p>Lorem ipsum dolor sit amet, consectetur adipiscing elit, sed do eiusmod dolore magna aliqua.</p></div>
  <div class="abs service" style="left:791px;top:1770px"><div class="icon" role="img" aria-label="Tire and wheel icon">
    <svg width="50" height="50" viewBox="0 0 50 50" fill="none" stroke="#fff" stroke-width="2.2"><circle cx="25" cy="25" r="21"/><circle cx="25" cy="25" r="11"/><path d="M10 10l30 30M40 10L10 40"/></svg></div>
    <h3>Tire and Wheel Services</h3><p>Lorem ipsum dolor sit amet, consectetur adipiscing elit, sed do eiusmod dolore magna aliqua.</p></div>
</section>

<section class="gallery">
  <div class="abs gallery-bg" role="img" aria-label="Dimmed workshop interior"></div>
  <div class="abs ticks" style="top:1978px"></div>
  <h2 class="abs center sec-title" style="top:2087px">Our <b>Gallery</b></h2>
  <p class="abs sec-desc" style="top:2147px">Sed ut perspiciatis unde omnis iste natus error sit voluptatem accusantium doloremque laudantium, totam rem aperiam, eaque ipsa quae ab illo inventore veritatis et quasi architecto beatae vitae dicta sunt explicabo.</p>
  <div class="abs tabs">
    <div class="tab active">Show All</div><div class="tab">Brakes</div><div class="tab">Suspension</div><div class="tab">Wheels</div><div class="tab">Steering</div>
  </div>
  <div class="shot" style="left:87px;top:2313px;width:322px;height:214px;background:radial-gradient(ellipse 120px 90px at 140px 110px,#8a7a66,transparent 80%),linear-gradient(135deg,#3a3834,#6e6658 60%,#4a4640)" role="img" aria-label="Mechanic working on a motorcycle"></div>
  <div class="shot" style="left:441px;top:2313px;width:318px;height:211px;background:radial-gradient(ellipse 90px 70px at 150px 120px,#c48c6c,transparent 80%),linear-gradient(135deg,#2c3442,#6c7888 50%,#a0aab6)" role="img" aria-label="Hand polishing a car panel"></div>
  <div class="shot" style="left:793px;top:2313px;width:317px;height:211px;background:radial-gradient(ellipse 90px 50px at 160px 110px,#1a1c20,#1a1c20 50%,transparent 80%),linear-gradient(135deg,#4e525a,#9ea4ac 60%,#cfd3d8)" role="img" aria-label="Battery being fitted in an engine bay"></div>
  <div class="shot" style="left:89px;top:2548px;width:318px;height:206px;background:radial-gradient(circle 90px at 110px 110px,#c6c8cc,#8a8e94 60%,transparent 62%),linear-gradient(135deg,#e07a30,#8a5a3a 60%,#4a4c50)" role="img" aria-label="Wheel nuts being tightened on an alloy wheel"></div>
  <div class="shot" style="left:441px;top:2548px;width:318px;height:206px;background:radial-gradient(circle 60px at 190px 90px,#5a5c60,transparent 80%),linear-gradient(135deg,#9a9ca0,#6a6c70 50%,#3e4044)" role="img" aria-label="Open gearbox with gears"></div>
  <div class="shot" style="left:793px;top:2548px;width:317px;height:206px;background:radial-gradient(ellipse 80px 90px at 100px 110px,#3c4656,transparent 80%),linear-gradient(135deg,#6c7480,#b4bac2 60%,#d4d8dc)" role="img" aria-label="Mechanics repairing a car front end"></div>
  <div class="abs ticks" style="top:2816px"></div>
</section>

<section class="partners">
  <h2 class="abs center sec-title" style="top:2892px">Our <b>Partners</b></h2>
  <p class="abs sec-desc" style="top:2946px;left:230px;width:740px;line-height:35px">Lorem ipsum dolor sit amet, consectetur adipiscing do eiusmod tempor incididunt ut labore et dolore magna. Ut enim ad minim veniam, quis nostrud exercitation ullamco</p>
  <div class="partner" style="left:114px">VASTINCO</div>
  <div class="partner" style="left:322px">DORFLINT</div>
  <div class="partner" style="left:530px">Q WRAP</div>
  <div class="partner" style="left:737px">GLENBRUSH</div>
  <div class="partner" style="left:945px">KEBO</div>
  <div class="abs pager">
    <svg width="12" height="16" viewBox="0 0 12 16"><path d="M9 2L3 8l6 6" stroke="#fff" stroke-width="2" fill="none"/></svg>
    <span class="dot"></span><span class="dot"></span><span class="dot on"></span><span class="dot"></span><span class="dot"></span>
    <svg width="12" height="16" viewBox="0 0 12 16"><path d="M3 2l6 6-6 6" stroke="#fff" stroke-width="2" fill="none"/></svg>
  </div>
  <div class="abs divider" style="top:3248px"></div>
</section>

<section class="blog">
  <h2 class="abs center sec-title" style="top:3324px">Our <b>Blog</b></h2>
  <article class="post" style="left:89px">
    <div class="img" style="background:radial-gradient(ellipse 120px 80px at 220px 60px,#d8d8da,transparent 80%),linear-gradient(135deg,#1c1e24,#3a3e48 50%,#a0a4aa)" role="img" aria-label="Technician polishing a car headlight"></div>
    <span class="date">Oct 27 2018</span>
    <h3>Sed ut perspiciatis unde omnis iste</h3>
    <p>Sed ut perspiciatis unde omnis iste natus error sit voluptatem accusantium doloremque laudantium, totam rem aperiam</p>
    <span class="more">Read More</span>
  </article>
  <article class="post" style="left:436px">
    <div class="img" style="background:radial-gradient(ellipse 90px 60px at 70px 110px,#d8322c,transparent 80%),radial-gradient(ellipse 90px 50px at 250px 150px,#f0f0f2,transparent 80%),linear-gradient(180deg,#8a8e94,#c8ccd2)" role="img" aria-label="Cars raised on lifts in a workshop"></div>
    <span class="date">Oct 27 2018</span>
    <h3>Sed ut perspiciatis unde omnis iste</h3>
    <p>Sed ut perspiciatis unde omnis iste natus error sit voluptatem accusantium doloremque laudantium, totam rem aperiam</p>
    <span class="more">Read More</span>
  </article>
  <article class="post" style="left:783px">
    <div class="img" style="background:radial-gradient(circle 70px at 160px 110px,#a8acb2,transparent 80%),linear-gradient(160deg,#f0a040,#c0603a 35%,#283a5c 75%,#1c2a48)" role="img" aria-label="Mechanic changing a car wheel"></div>
    <span class="date">Oct 27 2018</span>
    <h3>Sed ut perspiciatis unde omnis iste</h3>
    <p>Sed ut perspiciatis unde omnis iste natus error sit voluptatem accusantium doloremque laudantium, totam rem aperiam</p>
    <span class="more">Read More</span>
  </article>
</section>

<section class="appointment">
  <div class="abs appt-photo" role="img" aria-label="Assorted car parts and tools"></div>
  <div class="abs appt-band"></div>
  <div class="abs appt-title">Need Appointment</div>
  <div class="abs appt-text">Sed ut perspiciatis unde omnis iste natus sit voluptatem accusantium dolorem.</div>
  <div class="pill btn-dark" style="left:902px;top:3868px;width:206px;height:54px;font-size:16px">Get an Appointment
    <svg viewBox="0 0 20 20"><circle cx="10" cy="10" r="10" fill="#fff"/><path d="M8 5l5 5-5 5" stroke="#101216" stroke-width="2.5" fill="none"/></svg></div>
</section>

<footer>
  <div class="abs footer"></div>
  <div class="abs fcol" style="left:91px"><h4>CUSTOMER SERVICE</h4><ul><li>How It Works</li><li>Customisation</li><li>Delivery</li><li>Returns</li><li>Payment and security</li></ul></div>
  <div class="abs fcol" style="left:367px"><h4>QUICK LINKS</h4><ul><li>Home</li><li>About Us</li><li>Shop</li><li>FAQ &amp; Help</li></ul></div>
  <div class="abs fcol" style="left:624px"><h4>OTHER LINKS</h4><ul><li>Catalogue</li><li>Contact us</li><li>Blog</li><li>Privacy Policy</li></ul></div>
  <div class="abs fcol" style="left:865px"><h4>CONTACT US</h4></div>
  <div class="contact-row" style="top:4050px"><span class="ico"><svg width="14" height="18" viewBox="0 0 14 18"><path d="M7 0a7 7 0 0 0-7 7c0 5 7 11 7 11s7-6 7-11a7 7 0 0 0-7-7z" fill="#fff"/><circle cx="7" cy="7" r="2.5" fill="#e8342f"/></svg></span>Unit 4 Kestrel Works, Farrow Lane, Oakfield, Derbyshire, DE56 9QP</div>
  <div class="contact-row" style="top:4113px"><span class="ico"><svg width="16" height="12" viewBox="0 0 16 12"><rect width="16" height="12" fill="#fff"/><path d="M0 0l8 7 8-7" stroke="#e8342f" stroke-width="1.5" fill="none"/></svg></span>Email: sales@brenvashine.co.uk</div>
  <div class="contact-row" style="top:4168px"><span class="ico"><svg width="14" height="14" viewBox="0 0 14 14"><path d="M3 0l3 3-2 2c1 2 3 4 5 5l2-2 3 3-2 3C6 14 0 8 0 2z" fill="#fff"/></svg></span>Phone: 07700900418</div>
  <div class="abs bottombar"></div>
  <div class="abs legal">Site Map &nbsp;|&nbsp; Returns &nbsp;|&nbsp; Terms of use &nbsp;|&nbsp; Affiliate<br>Copyright © 2019. All Right Reserved.</div>
  <div class="abs pay">TILLWAVE</div>
</footer>

</body>
</html>
```